Wordpress 6 pages GLAM design for hair salon

Hi guys.
I need a glam & easy to navigate web design for my (women only) new hair salon.
I have a logo. You can see in attached files.
I like 3d backgrounds.
My favourite colours choice: any variety of pink(hot & very soft), white, black, grey.
I would like to see website very feminine, glamorous & kind of old Hollywood and Dorinda Calloway inspired.
Of course it should have plug ins, like social media, map, security etc.
My website now: http://velmoracoiffure.example

Designs what I like:
http://torvinellastudio.example
http://pelurabeautyloft.example
http://www.quillfernvisualworks.example/boutique-graphic-web-folio.html
Updates

Target Market(s)

WOMEN

Industry/Entity Type

Boutique

Requirements
Should not have
• any cartoon or other characters!

```html
<!DOCTYPE html>
<html lang="en">
<head>
<meta charset="utf-8">
<title>Velmora Coiffure</title>
<link href="https://fonts.googleapis.com/css2?family=Ubuntu:wght@300;400&display=swap" rel="stylesheet">
<style>
:root{
  --pink:#c24a74;
  --pink-deep:#b13b66;
  --pink-dark:#7f1e45;
  --pink-line:#d9759a;
  --pink-soft:#f0b9cd;
  --white:#ffffff;
  --paper:#f7f7f7;
  --ink:#4a4a4a;
}
*{margin:0;padding:0;box-sizing:border-box}
html,body{width:934px;height:1200px;overflow:hidden}
body{position:relative;background:var(--pink);font-family:"Ubuntu",sans-serif;font-weight:300;color:var(--white)}
.abs{position:absolute}
.topbar{left:0;top:0;width:934px;height:26px;background:var(--pink);font-size:10px}
.topbar .contact{position:absolute;top:7px;display:flex;align-items:center;gap:6px}
.header{left:0;top:26px;width:934px;height:241px;background:linear-gradient(#ffffff 0%,#fdfdfd 60%,#e6e6e6 100%)}
.brand{left:150px;top:96px;width:220px;text-align:center;color:var(--pink);font-size:22px;font-weight:400;letter-spacing:2px;line-height:1.2}
.nav{left:380px;top:53px;width:407px;height:33px;background:var(--pink);display:flex;align-items:center;padding-left:15px;gap:10px;font-size:10px;font-weight:400}
.nav a{color:var(--white);text-decoration:none;display:flex;align-items:center;gap:3px;position:relative;height:33px}
.nav a::before{content:"";width:4px;height:4px;border-radius:50%;background:var(--pink-soft)}
.nav a.active::after{content:"";position:absolute;left:0;right:-6px;bottom:0;height:2px;background:var(--white)}
.hero{left:408px;top:100px;width:350px;height:232px}
.slide-arrow{width:26px;height:26px;border-radius:50%;background:#eeeeee;border:1px solid #e2e2e2}
.about{left:147px;top:236px;width:220px;height:295px;background:linear-gradient(var(--pink) 0%,var(--pink-deep) 100%);border-radius:4px;box-shadow:0 2px 6px rgba(80,0,30,.35);padding:0 20px}
.about h2{font-weight:400;font-size:14px;text-align:center;margin-top:16px;padding-bottom:9px;border-bottom:1px solid var(--pink-line)}
.about p{font-size:8.6px;line-height:14.6px;text-align:justify;margin-top:9px;padding-bottom:6px}
.about p + p{margin-top:8px}
.avatar{left:217px;top:490px;width:82px;height:82px;border-radius:50%;background:var(--pink-deep);padding:4px}
.avatar div{width:100%;height:100%;border-radius:50%;background:radial-gradient(circle at 50% 40%,#f3d3c2,#9b6a55)}
.section-title{font-size:18px;font-weight:300;display:flex;align-items:center;gap:8px}
.section-title::after{content:"";flex:1;height:1px;background:var(--pink-line)}
.posts{left:147px;top:574px;width:220px}
.post{font-size:8.6px;line-height:14.6px;padding:12px 0 6px;border-bottom:1px solid var(--pink-line)}
.post:last-child{border-bottom:none}
.post time{display:block;text-align:right;color:var(--pink-soft)}
.welcome{left:380px;top:370px;width:407px;display:flex;align-items:center;gap:10px;font-size:18px}
.welcome .rule{flex:1;height:1px;background:var(--pink-line)}
.content{left:381px;top:405px;width:406px;height:300px;background:var(--paper);border-radius:3px;box-shadow:0 1px 4px rgba(80,0,30,.3);padding:20px 20px;color:var(--ink);font-size:8.6px;line-height:14.6px}
.content p{margin-bottom:14.6px;text-align:justify}
.content h3{color:var(--pink);font-weight:400;font-size:11px;margin:-2px 0 12px}
.read-more{position:absolute;right:20px;bottom:30px;width:92px;height:29px;background:var(--pink);border-radius:2px;display:flex;align-items:center;gap:10px;padding-left:7px;color:var(--white);font-size:10px}
.read-more span.ring{width:20px;height:20px;border-radius:50%;border:1px solid var(--pink-soft);display:flex;align-items:center;justify-content:center}
.gallery-title{left:147px;top:724px;width:640px}
.thumb{top:766px;width:139px;height:96px;background:var(--pink-deep);padding:5px;border-radius:2px}
.thumb div{width:100%;height:100%}
.g-arrow{top:800px}
.footer{left:0;top:893px;width:934px;height:200px;background:var(--pink-dark)}
.looks{left:147px;top:930px;display:grid;grid-template-columns:repeat(3,53px);gap:6px}
.looks div{width:53px;height:52px;background:linear-gradient(135deg,#e9e1dc,#3a2a26)}
.map{left:345px;top:930px;width:207px;height:109px;background:linear-gradient(135deg,#efe9dd,#e3ddd0)}
.map-card{left:394px;top:930px;width:151px;height:58px;background:var(--pink);border-radius:3px;padding:8px 10px;font-size:8.6px;line-height:14.6px}
.map-card::after{content:"";position:absolute;left:58px;bottom:-9px;border:9px solid transparent;border-top-color:var(--pink);border-bottom:0;border-left-width:0}
.touch{left:580px;top:927px;font-size:13px}
.touch-line{display:flex;align-items:center;gap:10px;font-size:10px;margin-top:10px}
.social{left:582px;top:1022px;display:flex;gap:6px}
.social span{width:16px;height:16px;border-radius:1px}
.copyright{left:147px;top:1053px;width:640px;display:flex;align-items:center;gap:12px;font-size:9px}
.copyright .rule{flex:1;height:1px;background:#9a3660}
.copyright .mark{color:#a13867;font-size:13px}
.bottom-band{left:0;top:1093px;width:934px;height:22px;background:var(--pink-deep)}
</style>
</head>
<body>

<div class="abs topbar">
  <div class="contact" style="left:552px">
    <svg width="9" height="13" viewBox="0 0 9 13"><rect x="0.5" y="0.5" width="8" height="12" rx="1" fill="none" stroke="#fff"/><line x1="3" y1="10.5" x2="6" y2="10.5" stroke="#fff"/></svg>
    555-014-2286
  </div>
  <div class="contact" style="left:642px">
    <svg width="12" height="9" viewBox="0 0 12 9"><rect width="12" height="9" fill="#f0b9cd"/><path d="M0 0 6 5 12 0" fill="none" stroke="#c24a74"/></svg>
    info@velmoracoiffure.example
  </div>
</div>

<header class="abs header"></header>
<div class="abs brand">VELMORA<br>COIFFURE</div>

<nav class="abs nav">
  <a class="active" href="#">Home</a>
  <a href="#">About us</a>
  <a href="#">Services</a>
  <a href="#">Gallery</a>
  <a href="#">Blog</a>
  <a href="#">Contacts</a>
</nav>

<svg class="abs hero" viewBox="0 0 350 232" role="img" aria-label="Portrait of a woman with voluminous curly auburn updo">
  <defs>
    <linearGradient id="heroFill" x1="0" y1="0" x2="1" y2="0">
      <stop offset="0" stop-color="#ffffff"/>
      <stop offset="0.45" stop-color="#f3ddd2"/>
      <stop offset="1" stop-color="#6b3a26"/>
    </linearGradient>
  </defs>
  <ellipse cx="175" cy="115" rx="173" ry="113" fill="#c24a74"/>
  <ellipse cx="175" cy="112" rx="167" ry="106" fill="url(#heroFill)"/>
</svg>
<div class="abs slide-arrow" style="left:380px;top:201px"></div>
<div class="abs slide-arrow" style="left:760px;top:201px"></div>

<section class="abs about">
  <h2>A Few Words About Me</h2>
  <p>Certified Hair Stylist with European and Canadian experience</p>
  <p>Finalist of the Lumière 2013 - The National Hairstylist of the Year Awards.</p>
  <p style="border-bottom:1px solid var(--pink-line);padding-bottom:10px">Leading Stylist at fashion shows and photo shoots Trained by Brightwell Beauty School, Harlow Cutting School (Canada), Lunavell Hair Extensions Certification (Canada), Solenne Color School (Italy), European Hairstyle School, Ravensby School (Europe)</p>
</section>
<div class="abs avatar" role="img" aria-label="Portrait photo of the stylist"><div></div></div>

<section class="abs posts">
  <h2 class="section-title">New Post</h2>
  <div class="post">“The Polished Edit” by Celia Marchbank. A stylist`s notes on lasting shine and volume...<time>December 14, 2013</time></div>
  <div class="post">“The Polished Edit” by Celia Marchbank. A stylist`s notes on lasting shine and volume...<time>December 14, 2013</time></div>
</section>

<div class="abs welcome">
  <span class="rule"></span>
  <svg width="18" height="8" viewBox="0 0 18 8"><path d="M0 4H18M12 0 16 4 12 8" fill="none" stroke="#d9759a"/></svg>
  <span>Welcome To Our Website!</span>
  <svg width="18" height="8" viewBox="0 0 18 8"><path d="M0 4H18M6 0 2 4 6 8" fill="none" stroke="#d9759a"/></svg>
  <span class="rule"></span>
</div>

<article class="abs content">
  <p>Our salon is based on the belief that our customers' needs are of the utmost importance. Our team is committed to meeting those needs. As a result, a high percentage of our business is from repeat customers and referrals.</p>
  <p>We would welcome the opportunity to earn your trust and deliver you the best service in the industry!</p>
  <h3>The Stylist/colorist</h3>
  <p>A professional stylist/colorist is fundamentally different from the classic hairdresser. The name of the profession comes from the word” color”, because the colorist specializes in hair coloring. Moreover, the procedure of dying with colorist has an independent title “coloring” to emphasize the difference from the classical multi-tone hair coloring. The stylist/colorist selects not one color, but the range of matching colors, taking into account not only the wishes of the client, but also the color of his eyes and skin.</p>
  <a class="read-more"><span class="ring"><svg width="6" height="8" viewBox="0 0 6 8"><path d="M1 0 5 4 1 8" fill="none" stroke="#f0b9cd"/></svg></span>Read More</a>
</article>

<h2 class="abs section-title gallery-title">Our Gallery</h2>
<svg class="abs g-arrow" style="left:146px" width="14" height="28" viewBox="0 0 14 28"><path d="M13 0 1 14 13 28" fill="none" stroke="#d9759a"/></svg>
<svg class="abs g-arrow" style="left:773px" width="14" height="28" viewBox="0 0 14 28"><path d="M1 0 13 14 1 28" fill="none" stroke="#d9759a"/></svg>
<div class="abs thumb" style="left:167px"><div role="img" aria-label="Salon interior with styling stations" style="background:linear-gradient(135deg,#e8e4e0,#8e3a3a)"></div></div>
<div class="abs thumb" style="left:320px"><div role="img" aria-label="Salon reception with product shelves" style="background:linear-gradient(135deg,#f2efea,#9c3a38)"></div></div>
<div class="abs thumb" style="left:474px"><div role="img" aria-label="Salon storefront window" style="background:linear-gradient(135deg,#3a3a3a,#c9cfd6)"></div></div>
<div class="abs thumb" style="left:629px"><div role="img" aria-label="Salon entrance sign near parking stairs" style="background:linear-gradient(135deg,#d9d3c6,#5b4a3a)"></div></div>

<footer class="abs footer"></footer>
<div class="abs looks" role="img" aria-label="Six hairstyle portraits">
  <div></div><div></div><div></div><div></div><div></div><div></div>
</div>
<div class="abs map" role="img" aria-label="Street map showing the salon location"></div>
<svg class="abs" style="left:430px;top:1003px" width="12" height="17" viewBox="0 0 12 17"><path d="M6 17C6 17 0 9 0 6a6 6 0 0 1 12 0c0 3-6 11-6 11z" fill="#c24a74"/><circle cx="6" cy="6" r="2.2" fill="#fff"/></svg>
<div class="abs map-card">Velmora Coiffure<br>555-014-2286<br>info@velmoracoiffure.example</div>

<div class="abs touch">
  Keep In Touch
  <div class="touch-line" style="margin-top:12px">
    <svg width="20" height="22" viewBox="0 0 20 22"><rect x="1" y="1" width="11" height="20" rx="1.5" fill="none" stroke="#d9759a"/><rect x="8" y="9" width="11" height="12" fill="none" stroke="#d9759a"/></svg>
    555-014-2286
  </div>
  <div class="touch-line" style="margin-top:4px">
    <svg width="22" height="14" viewBox="0 0 22 14"><rect width="22" height="14" fill="#d9759a"/><path d="M0 0 11 8 22 0" fill="none" stroke="#7f1e45"/></svg>
    info@velmoracoiffure.example
  </div>
</div>
<div class="abs social">
  <span style="background:#d9759a"></span>
  <span style="background:#d9759a"></span>
  <span style="background:#d9759a"></span>
</div>

<div class="abs copyright">
  <span>Copyright © 2012 velmoracoiffure.example</span>
  <span class="rule"></span>
  <span class="mark">Velmora Coiffure</span>
</div>

<div class="abs bottom-band"></div>

</body>
</html>
```